Vantoq Business Card Project showing the logo and a marbo image on the rear

Design a whacky but professional business card, the logo is for the front and the Marbo image is for the rear. Happy to consider other open source Marbo Images if the designer wants to select one from the web. Vantoq is a competitor to OMB.com.au and Pellory.com.au and is based around every property in Australia

Target Market(s)

Business

Contact Information for Business Card

Name, Title, Email, Web, Phone Number

Font styles to use
Other font styles liked:
• avenir

Requirements
Must have
• Image on Back logo on front
Nice to have
• Happy to consider other images on rear, preftably Colin Marbo. Image supplied I own, we can use open source other Marbo Images

```html
<!DOCTYPE html>
<html lang="en">
<head>
<meta charset="utf-8">
<title>Vantoq Business Card</title>
<link href="https://fonts.googleapis.com/css2?family=Jost:wght@400;600&family=Roboto:wght@400;500&display=swap" rel="stylesheet">
<style>
  :root {
    --stage: #2b2b2b;
    --card: #f0f0ef;
    --ink: #151515;
    --orange: #ef8a12;
    --text: #222222;
    --faint: rgba(200, 200, 200, 0.28);
  }
  * { margin: 0; padding: 0; box-sizing: border-box; }
  html, body { width: 1200px; height: 1138px; overflow: hidden; background: var(--stage); }
  .canvas { position: relative; width: 1200px; height: 1138px; }

  .card {
    position: absolute;
    background: var(--card);
    border-radius: 13px;
    overflow: hidden;
  }
  .card--front { left: 274px; top: 186px; width: 622px; height: 376px; }
  .card--back  { left: 276px; top: 608px; width: 618px; height: 374px; }

  .brand {
    position: absolute;
    display: flex;
    align-items: center;
    font-family: "Jost", "Avenir", sans-serif;
    font-weight: 600;
    color: var(--ink);
    line-height: 1;
  }
  .brand__dot { border-radius: 50%; background: var(--orange); flex: none; }

  .front__brand { left: 0; right: 0; top: 72px; justify-content: center; font-size: 68px; gap: 20px; }
  .front__brand .brand__dot { width: 56px; height: 56px; }
  .front__url {
    position: absolute; left: 0; right: 0; top: 138px;
    text-align: center;
    font-family: "Jost", "Avenir", sans-serif;
    font-size: 17px; letter-spacing: 12px;
    color: var(--ink);
  }
  .front__artwork {
    position: absolute; left: 0; right: 0; top: 198px; bottom: 0;
    background: linear-gradient(180deg, #f0f0ef 0%, #e45fa0 18%, #f07a5a 40%, #c9d94a 62%, #6fc5d6 80%, #7cc143 100%);
  }

  .back__tab {
    position: absolute; left: -13px; top: 48px;
    width: 26px; height: 68px; border-radius: 0 34px 34px 0;
    background: var(--orange);
  }
  .back__decor {
    position: absolute; left: 282px; top: 6px;
    width: 330px; height: 330px; border-radius: 50%;
    background: var(--faint);
  }
  .person { position: absolute; left: 26px; top: 56px; font-family: "Roboto", sans-serif; }
  .person__name { font-size: 24px; font-weight: 500; color: var(--orange); line-height: 1.2; }
  .person__title { font-size: 16px; color: var(--text); margin-top: 2px; }

  .address {
    position: absolute; left: 26px; top: 220px;
    font-family: "Roboto", sans-serif; font-size: 16.5px; line-height: 22px; color: var(--text);
    font-style: normal;
  }
  .contacts {
    position: absolute; left: 26px; top: 277px;
    list-style: none;
    font-family: "Roboto", sans-serif; font-size: 16.5px; color: var(--text);
  }
  .contacts li { display: flex; align-items: center; height: 24px; }
  .contacts svg { width: 14px; height: 14px; margin-left: 2px; margin-right: 15px; fill: none; stroke: var(--orange); stroke-width: 1.8; }
  .contacts .accent { color: var(--orange); }

  .back__brand { left: 328px; top: 298px; font-size: 56px; gap: 16px; }
  .back__brand .brand__dot { width: 46px; height: 46px; }
</style>
</head>
<body>
<main class="canvas">
  <section class="card card--front">
    <div class="brand front__brand"><span class="brand__dot"></span><span>Vantoq</span></div>
    <p class="front__url">www.vantoq.com</p>
    <div class="front__artwork" role="img" aria-label="Colourful Marbo-style city illustration of cartoon buildings and a tram along the bottom of the card"></div>
  </section>

  <section class="card card--back">
    <span class="back__tab"></span>
    <span class="back__decor"></span>
    <div class="person">
      <h1 class="person__name">Reid Calloway</h1>
      <p class="person__title">Founder &amp; CEO</p>
    </div>
    <address class="address">Level 4, 18 Harlow Lane,<br>Sydney 2000, Australia</address>
    <ul class="contacts">
      <li>
        <svg viewBox="0 0 16 16"><circle cx="8" cy="8" r="6.8"/><path d="M5.5 4.8l1.3-.3.8 1.8-.9.7a4.5 4.5 0 0 0 2.3 2.3l.7-.9 1.8.8-.3 1.3c-3.3.3-6-2.4-5.7-5.7z"/></svg>
        <span>(00) 4817 2950</span>
      </li>
      <li>
        <svg viewBox="0 0 16 16"><rect x="1.5" y="3.5" width="13" height="9"/><path d="M1.5 3.5L8 9l6.5-5.5"/></svg>
        <span>calloway@vantoq.com</span>
      </li>
      <li>
        <svg viewBox="0 0 16 16"><circle cx="8" cy="8" r="6.5"/><ellipse cx="8" cy="8" rx="2.8" ry="6.5"/><path d="M1.5 8h13"/></svg>
        <span>www.<span class="accent">vantoq</span>.com</span>
      </li>
    </ul>
    <div class="brand back__brand"><span class="brand__dot"></span><span>Vantoq</span></div>
  </section>
</main>
</body>
</html>
```